Machinery Harbor Corp - Business Card Design

Need a new modern designed business card that is different and stands out to represent my equipment financing company. Machinery Harbor Corp finances all types of equipment and all types of industries. We like to do equipment financing a different way by putting customers first and want our card to represent that different approach to business. I want a card that some remembers when they receive it so it sticks in their mind and makes that wow impression.

Card should have a black background so the logo stands out. It can be horizontial or vertical or a combination of both.

Front of card information is below that shows the information that would go on my card. That is where I want a different look or design to stand out. The front could be split black/orange colour so the logo could pop on black side and information on orange side with different lettering. Just outside the box thinking on the front of the card. Open to any type of design.

Back of card is below which i I like unless you have a different spin to provide or a different idea that would make the card better as I am open to anything that looks great.

Target Market(s)

Machinery Harbor Corp deals with business owners in all industries.

Industry/Entity Type

Business

Contact Information for Business Card

Colors

Designer to choose colors to be used in the design.

Requirements
Must have
• Modern
• Different
• Stand Out
• Makes an Impression

```html
<!DOCTYPE html>
<html lang="en">
<head>
<meta charset="utf-8">
<title>Machinery Harbor Corp – Business Card</title>
<link rel="stylesheet" href="https://fonts.googleapis.com/css2?family=Cinzel:wght@400&family=Lato:wght@400;700&display=swap">
<style>
  :root {
    --stage: #2b2b2b;
    --card-black: #050505;
    --orange-light: #f7941d;
    --orange-deep: #ee3f23;
    --orange-text: #f26a21;
    --white: #ffffff;
    --ink: #0a0a0a;
    --grey-text: #9a9a9a;
  }
  * { box-sizing: border-box; margin: 0; padding: 0; }
  html, body {
    width: 1200px;
    height: 800px;
    overflow: hidden;
    background: var(--stage);
  }
  .stage {
    width: 1200px;
    height: 800px;
    display: flex;
    align-items: center;
    justify-content: center;
    gap: 80px;
  }
  .card {
    position: relative;
    width: 460px;
    height: 460px;
    border-radius: 34px;
    overflow: hidden;
    box-shadow: 0 16px 40px rgba(0,0,0,0.45);
  }

  /* Front: orange side with wordmark */
  .card--front {
    background: linear-gradient(225deg, var(--orange-light) 0%, #f26a21 50%, var(--orange-deep) 100%);
    display: flex;
    align-items: center;
    justify-content: center;
  }
  .wordmark {
    font-family: "Cinzel", serif;
    font-weight: 400;
    color: var(--ink);
    text-align: center;
    line-height: 1.1;
  }
  .wordmark__main {
    display: block;
    font-size: 44px;
    letter-spacing: 2px;
  }
  .wordmark__sub {
    display: block;
    font-size: 24px;
    letter-spacing: 9px;
    margin-top: 8px;
  }

  /* Back: black side with contact details */
  .card--back {
    background: var(--card-black);
  }
  .card__swoosh {
    position: absolute;
    inset: 0;
    width: 100%;
    height: 100%;
  }
  .contact {
    position: absolute;
    top: 58px;
    right: 44px;
    text-align: right;
  }
  .contact__company {
    font-family: "Cinzel", serif;
    font-weight: 400;
    color: var(--orange-text);
    line-height: 1.1;
  }
  .contact__company-main {
    display: block;
    font-size: 34px;
    letter-spacing: 1px;
  }
  .contact__company-sub {
    display: block;
    font-size: 18px;
    letter-spacing: 7px;
    color: var(--grey-text);
    margin-top: 4px;
  }
  .contact__name {
    font-family: "Lato", sans-serif;
    font-weight: 700;
    font-size: 26px;
    color: var(--white);
    letter-spacing: 0.5px;
    margin-top: 30px;
  }
  .contact__role {
    font-family: "Lato", sans-serif;
    font-weight: 400;
    font-size: 15px;
    color: var(--white);
    letter-spacing: 1px;
    margin-top: 2px;
  }
  .contact__details {
    list-style: none;
    margin-top: 34px;
    font-family: "Lato", sans-serif;
    font-size: 15px;
    line-height: 1.6;
    color: var(--white);
  }
  .contact__web { color: var(--orange-text); }
</style>
</head>
<body>
  <main class="stage">
    <section class="card card--front" aria-label="Card front">
      <h1 class="wordmark">
        <span class="wordmark__main">MACHINERY</span>
        <span class="wordmark__sub">HARBOR CORP</span>
      </h1>
    </section>

    <section class="card card--back" aria-label="Card back">
      <svg class="card__swoosh" viewBox="0 0 460 460" aria-hidden="true">
        <defs>
          <linearGradient id="swooshOrange" x1="0" y1="0" x2="1" y2="1">
            <stop offset="0" stop-color="#f7941d"/>
            <stop offset="1" stop-color="#ee3f23"/>
          </linearGradient>
        </defs>
        <path d="M0 110 C 50 280 170 400 330 460 L 0 460 Z" fill="#ffffff"/>
        <path d="M0 140 C 45 300 160 410 300 460 L 0 460 Z" fill="#050505"/>
        <path d="M0 170 C 40 315 150 420 270 460 L 0 460 Z" fill="url(#swooshOrange)"/>
      </svg>
      <div class="contact">
        <p class="contact__company">
          <span class="contact__company-main">MACHINERY</span>
          <span class="contact__company-sub">HARBOR CORP</span>
        </p>
        <p class="contact__name">DEAN MARLOW</p>
        <p class="contact__role">PRESIDENT</p>
        <ul class="contact__details">
          <li>555.014.2290</li>
          <li>dean@machineryharborcorp.ca</li>
          <li class="contact__web">www.machineryharborcorp.ca</li>
        </ul>
      </div>
    </section>
  </main>
</body>
</html>
```